Moxy Fen needs some awesome stationary

Do you have what it takes to get my brand? You either do or you don't, have a crack at a design and you my just win my business.

I don't want to waste your or my time, so put your creative genius on either a business card or envelope.

I however need a package of stationary that follows the same brand. I will message you to complete the remaining should I like your first submission.

Here is what I need, have a go!

Basically I need the following for my small business based in melbourne.
- Letterhead (printer ready and MS Word)
- Business Card
- Compliments Slip
- Envelope
- Proposal Cover Page (MS Word only)
- Presentation Folder
- Marbled Fox Cards
- Student Name Tent
- Index Cards
- Vell-Ka

I am establishing the brand and it must be modern, professional but also relaxed; that is not formal and not corporate. It represents a company are leaders, but small enough to care and operate like a bunch of friends. We are bringing people and conversations back to business, and turfing out all the bureaucracy and crazy and wasteful procedures. Its about "lets talk and figure it out together and find even better ways".

Target Market(s)

Mainly companies that build software products, but Agile practices are used in many other industries (even graphic design projects)

Industry/Entity Type

Information Technology

Font styles to use
Sans Serif

Colors
3176b5
aaaaaa

Requirements
Must have
• I like curves and circles and not boxes or rectangles.
• I want a colour rich design with my brand colours, but it must be balanced.
• I want more modern than traditional, but simple modern
Should not have
• Not corporate
• Please don't waste my time if your not going to think about it.
• Don't mess with my primary logo
• Don't change my colours
• Don't overlay logo on image

```html
<!DOCTYPE html>
<html lang="en">
<head>
<meta charset="utf-8">
<title>Moxy Fen – Index Cards and Name Tents</title>
<link rel="stylesheet" href="https://fonts.googleapis.com/css2?family=Open+Sans:wght@400;600;700&display=swap">
<style>
  :root {
    --backdrop: #8a8b8f;
    --paper: #ffffff;
    --brand-blue: #2c5ca4;
    --brand-coral: #ff8080;
    --brand-grey: #a7aebb;
    --rule: #555555;
    --ring: #b8b8b8;
    --fold: #c9c9c9;
    --ink-soft: #444444;
  }
  * { margin: 0; padding: 0; box-sizing: border-box; }
  html, body {
    width: 1190px;
    height: 1200px;
    overflow: hidden;
    background: var(--backdrop);
    font-family: "Open Sans", Arial, sans-serif;
  }
  .stage { position: relative; width: 1190px; height: 1200px; }

  /* Index cards */
  .index-card {
    position: absolute;
    top: 99px;
    width: 457px;
    height: 543px;
    background: var(--paper);
    box-shadow: 0 2px 5px rgba(0,0,0,0.25);
  }
  .index-card--blue { left: 120px; --accent: var(--brand-blue); }
  .index-card--coral { left: 632px; --accent: var(--brand-coral); }
  .index-card__header {
    height: 74px;
    background: var(--accent);
  }
  .index-card__rule {
    position: absolute;
    left: 35px;
    right: 34px;
    border-top: 1px dotted var(--rule);
  }
  .index-card__footer {
    position: absolute;
    left: 28px;
    top: 494px;
    display: flex;
    align-items: center;
  }
  .brand-mark {
    display: flex;
    align-items: center;
    gap: 6px;
    font-weight: 700;
    color: var(--brand-blue);
  }
  .brand-mark__dot {
    width: 16px;
    height: 16px;
    border-radius: 50%;
    background: var(--brand-blue);
  }
  .brand-mark--small { font-size: 18px; }
  .tagline {
    margin-left: 55px;
    font-size: 12.5px;
    color: var(--ink-soft);
  }
  .index-card__stamp {
    position: absolute;
    left: 358px;
    top: 462px;
    width: 66px;
    height: 66px;
    border-radius: 50%;
    border: 1px solid var(--ring);
  }

  /* Name tents */
  .name-tent {
    position: absolute;
    left: 195px;
    width: 738px;
    height: 133px;
  }
  .name-tent--a { top: 757px; }
  .name-tent--b { top: 956px; }
  .name-tent__art { position: absolute; inset: 0; }
  .name-tent__name {
    position: absolute;
    left: 240px;
    top: 50%;
    transform: translateY(-50%);
    font-size: 70px;
    font-weight: 600;
    letter-spacing: 0.5px;
    color: var(--brand-blue);
    line-height: 1;
    white-space: nowrap;
  }
  .brand-stack {
    position: absolute;
    display: flex;
    flex-direction: column;
    align-items: center;
    gap: 5px;
    font-size: 17px;
    font-weight: 700;
    white-space: nowrap;
  }
  .brand-stack__dot {
    width: 44px;
    height: 44px;
    border-radius: 50%;
  }
  .name-tent--a .brand-stack { left: 110px; top: 30px; color: var(--brand-blue); }
  .name-tent--a .brand-stack__dot { background: var(--brand-blue); }
  .name-tent--b .brand-stack { left: 55px; top: 30px; color: var(--paper); }
  .name-tent--b .brand-stack__dot { background: var(--paper); }
</style>
</head>
<body>
<main class="stage">

  <section class="index-card index-card--blue">
    <div class="index-card__header"></div>
    <div class="index-card__rule" style="top:118px"></div>
    <div class="index-card__rule" style="top:181px"></div>
    <div class="index-card__rule" style="top:243px"></div>
    <div class="index-card__rule" style="top:306px"></div>
    <div class="index-card__rule" style="top:370px"></div>
    <div class="index-card__rule" style="top:431px"></div>
    <div class="index-card__footer">
      <div class="brand-mark brand-mark--small"><span class="brand-mark__dot"></span>Moxy Fen</div>
      <span class="tagline">Get It Done</span>
    </div>
    <div class="index-card__stamp"></div>
  </section>

  <section class="index-card index-card--coral">
    <div class="index-card__header"></div>
    <div class="index-card__rule" style="top:118px"></div>
    <div class="index-card__rule" style="top:181px"></div>
    <div class="index-card__rule" style="top:243px"></div>
    <div class="index-card__rule" style="top:306px"></div>
    <div class="index-card__rule" style="top:370px"></div>
    <div class="index-card__rule" style="top:431px"></div>
    <div class="index-card__footer">
      <div class="brand-mark brand-mark--small"><span class="brand-mark__dot"></span>Moxy Fen</div>
      <span class="tagline">Get It Done</span>
    </div>
    <div class="index-card__stamp"></div>
  </section>

  <section class="name-tent name-tent--a">
    <svg class="name-tent__art" width="738" height="133" viewBox="0 0 738 133" aria-hidden="true">
      <polygon points="39,0 0,109 39,109" fill="var(--fold)"/>
      <rect x="39" y="0" width="699" height="133" fill="var(--brand-blue)"/>
      <path d="M86,0 H738 V133 H150 C80,118 45,60 86,0 Z" fill="var(--brand-grey)" transform="translate(-10,6)"/>
      <path d="M93,0 H738 V133 H185 C100,118 55,60 93,0 Z" fill="var(--paper)"/>
    </svg>
    <div class="brand-stack"><span class="brand-stack__dot"></span>Moxy Fen</div>
    <div class="name-tent__name">ALEX RIVER</div>
  </section>

  <section class="name-tent name-tent--b">
    <svg class="name-tent__art" width="738" height="133" viewBox="0 0 738 133" aria-hidden="true">
      <polygon points="39,0 0,109 39,109" fill="var(--fold)"/>
      <rect x="39" y="0" width="699" height="133" fill="var(--brand-blue)"/>
      <path d="M208,0 H738 V133 H268 C205,118 170,55 208,0 Z" fill="var(--brand-grey)" transform="translate(-8,6)"/>
      <path d="M214,0 H738 V133 H300 C220,118 180,55 214,0 Z" fill="var(--paper)"/>
    </svg>
    <div class="brand-stack"><span class="brand-stack__dot"></span>Moxy Fen</div>
    <div class="name-tent__name">ALEX RIVER</div>
  </section>

</main>
</body>
</html>
```